Asphalt Driveway Billboard Design

We need a billboard designed for an Asphalt & Concrete Company in Minnesota. We want to advertise Asphalt Driveways on this billboard! Logo is uploaded below. Our website is pinecrest-paving.com for more information.

```html
<!DOCTYPE html>
<html lang="en">
<head>
<meta charset="utf-8">
<title>Pinecrest Asphalt &amp; Concrete Billboard</title>
<link rel="stylesheet" href="https://fonts.googleapis.com/css2?family=Bebas+Neue&family=Montserrat:wght@600;700;800&display=swap">
<style>
  :root {
    --brand-blue: #1a5ca8;
    --brand-blue-light: #3a9ad9;
    --ink: #111318;
    --paper: #ffffff;
    --page: #eef1f5;
    --grass: #4f8a2e;
    --sky: #b9d6ee;
    --asphalt: #2a2b2e;
    --badge-gold: #d8b43a;
    --badge-green: #5d9b3a;
  }
  * { box-sizing: border-box; margin: 0; padding: 0; }
  html, body { width: 1050px; height: 1200px; overflow: hidden; background: var(--page); }
  .billboard {
    position: absolute; left: 25px; top: 350px; width: 1000px; height: 500px;
    background: var(--paper); overflow: hidden;
    box-shadow: 0 6px 18px rgba(0,0,0,.18);
    font-family: "Montserrat", sans-serif;
  }
  .driveway-photo {
    position: absolute; left: 0; top: 135px; width: 740px; height: 305px;
    background:
      linear-gradient(180deg, rgba(255,255,255,1) 0%, rgba(255,255,255,0) 22%),
      linear-gradient(180deg, var(--sky) 0%, #d9d3c6 38%, #8a8276 55%, var(--grass) 70%, var(--asphalt) 85%, var(--asphalt) 100%);
  }
  .brand {
    position: absolute; left: 20px; top: 100px; width: 170px; text-align: center; color: var(--ink);
  }
  .brand-name { font-weight: 800; font-size: 27px; letter-spacing: 0.5px; line-height: 1; }
  .brand-tag { font-weight: 700; font-size: 9.5px; letter-spacing: 0.6px; margin-top: 3px; }
  .headline {
    position: absolute; left: 270px; top: 38px; width: 400px; text-align: center;
    color: var(--brand-blue); font-weight: 800; font-size: 37px; line-height: 1.12; letter-spacing: 0.3px;
  }
  .partner-strip { position: absolute; left: 0; top: 440px; width: 720px; height: 60px; }
  .panel-art { position: absolute; inset: 0; }
  .license {
    position: absolute; left: 738px; top: 40px; width: 262px; height: 38px; padding-right: 15px;
    text-align: right; color: var(--paper);
  }
  .license-label { font-weight: 700; font-size: 9.5px; padding-top: 4px; }
  .license-number { font-weight: 800; font-size: 15px; line-height: 1.1; }
  .contact { position: absolute; left: 725px; width: 275px; text-align: center; }
  .contact-label { color: var(--brand-blue); font-weight: 800; font-size: 22px; line-height: 1; }
  .contact-value { color: var(--brand-blue); font-family: "Bebas Neue", sans-serif; line-height: 1; }
  .tel { top: 100px; }
  .tel .contact-value { font-size: 58px; margin-top: 6px; }
  .email { top: 206px; }
  .web { top: 294px; }
  .email .contact-value, .web .contact-value { font-size: 27px; margin-top: 4px; }
</style>
</head>
<body>
  <main class="billboard">
    <div class="driveway-photo" role="img" aria-label="Photo of a stone-and-siding family home with a freshly sealed black asphalt driveway and green lawn under a blue sky"></div>

    <div class="brand">
      <div class="brand-name">PINECREST</div>
      <div class="brand-tag">— ASPHALT &amp; CONCRETE —</div>
    </div>

    <h1 class="headline">PREMIER ASPHALT<br>&amp; CONCRETE<br>CONTRACTOR</h1>

    <svg class="partner-strip" viewBox="0 0 720 60" aria-label="Partner and accreditation badges">
      <rect x="0" y="0" width="720" height="60" fill="#ffffff"/>
      <rect x="30" y="18" width="82" height="24" rx="4" fill="#8fa3c8"/>
      <rect x="160" y="12" width="122" height="36" rx="4" fill="#1f5a93"/>
      <rect x="325" y="16" width="180" height="28" rx="14" fill="#c9ccd3"/>
      <rect x="520" y="16" width="150" height="28" rx="4" fill="#f28a21"/>
    </svg>

    <svg class="panel-art" viewBox="0 0 1000 500" aria-hidden="true">
      <defs>
        <linearGradient id="licenseBand" x1="0" x2="1" y1="0" y2="0">
          <stop offset="0" stop-color="var(--brand-blue-light)"/>
          <stop offset="1" stop-color="var(--brand-blue)"/>
        </linearGradient>
      </defs>
      <path d="M740,0 L1000,0 L1000,500 L770,500 C705,320 708,120 740,0Z" fill="var(--paper)"/>
      <path d="M683,0 L740,0 C708,120 705,320 770,500 L725,500 C665,340 660,130 683,0Z" fill="var(--brand-blue)"/>
      <path d="M718,270 C722,370 742,440 784,500 L760,500 C730,440 716,370 718,270Z" fill="var(--brand-blue-light)"/>
      <path d="M734,40 L1000,40 L1000,78 L728,78 C729,65 731,52 734,40Z" fill="url(#licenseBand)"/>
      <g class="award-badges">
        <circle cx="772" cy="405" r="16" fill="var(--badge-green)"/>
        <circle cx="800" cy="405" r="19" fill="#7fae4a"/>
        <circle cx="832" cy="405" r="20" fill="var(--badge-green)"/>
        <circle cx="862" cy="405" r="21" fill="var(--badge-gold)"/>
        <circle cx="894" cy="405" r="19" fill="#7fae4a"/>
        <circle cx="924" cy="405" r="18" fill="var(--badge-gold)"/>
        <circle cx="954" cy="405" r="17" fill="var(--badge-green)"/>
        <circle cx="862" cy="405" r="14" fill="#3f7a2a"/>
      </g>
    </svg>

    <div class="license">
      <div class="license-label">RESIDENTIAL BLDG CONTRACTOR LIC.</div>
      <div class="license-number">#BC714306.</div>
    </div>

    <div class="contact tel">
      <div class="contact-label">TEL:</div>
      <div class="contact-value">763-555-0148</div>
    </div>
    <div class="contact email">
      <div class="contact-label">EMAIL:</div>
      <div class="contact-value">SALES@PINECREST-PAVING.COM</div>
    </div>
    <div class="contact web">
      <div class="contact-label">WEB:</div>
      <div class="contact-value">SALES@PINECREST-PAVING.COM</div>
    </div>
  </main>
</body>
</html>
```